Stationery Design Project for High End Wealth Management Firm

We need a stationery design for our high-end wealth management firm. Our clientele are affluent and our brand is built around providing investment services with world-class service.

The final concepts should provide a business card, letterhead, and envelope.

We like the idea of having text on the front and back and we MUST have black front and back business cards.
For the business card we have the following that needs to be included:
Company Logo & Tagline
Employee Name
Employee title
Employee Email
Website
2 seperate office cities, addresses, and phone numbers
Financial disclosure (small print)

Having black envelopes would be neat, but black is not a must for the envelopes.
Updates

Project Deadline Extended
Reason: To give the concept one more day of revisions.

Project Deadline Extended
Reason: To allow for more concepts and designs.

Target Market(s)

High Net Worth

Industry/Entity Type

Business

Requirements
Must have
• The following disclosure must be on the back of the card in small print:

Investment Advisory Services offered through Harrowfield Asset Partners LLC, a NFR Registered Investment Advisor. Vantory Wealth Management LLC is not affiliated with Harrowfield Asset Partners LLC.

Black business cards are also a must have.

Please utilize each of the 3 components of our logo in the design.

Please use our white background logo elements when designing our letterhead if you need them.
Nice to have
• Please use our company colors when designing. Utilize a combination of the elements of our logo that we have attached.

We are going to be printing our business cards on letterpress.

```html
<!DOCTYPE html>
<html lang="en">
<head>
<meta charset="utf-8">
<title>Vantory Wealth Management – Business Card Options</title>
<link rel="stylesheet" href="https://fonts.googleapis.com/css2?family=Marcellus&family=Arimo:wght@400;700&display=swap">
<style>
  :root {
    --board-green: #66b947;
    --card-black: #0b0909;
    --card-glow: #3a3636;
    --silver: #cfcfcf;
    --gold: #f3c65c;
    --gold-deep: #c98a2c;
    --gold-light: #f6d27a;
    --yellow-box: #fcd45b;
    --ink: #111111;
    --white: #ffffff;
  }
  * { box-sizing: border-box; margin: 0; padding: 0; }
  html, body {
    width: 1200px; height: 747px; overflow: hidden;
    background: var(--board-green);
  }
  .board { position: relative; width: 1200px; height: 747px; }

  .option-label {
    position: absolute;
    font-family: "Arimo", Arial, sans-serif;
    font-weight: 700; font-size: 22px; color: var(--ink);
  }

  .card {
    position: absolute; width: 520px; height: 296px;
    border-radius: 22px; overflow: hidden;
    background: radial-gradient(ellipse 60% 65% at 50% 45%, var(--card-glow) 0%, #1a1616 55%, var(--card-black) 100%);
    box-shadow: 3px 4px 7px rgba(0,0,0,.45);
  }

  .wordmark {
    position: absolute; display: flex; align-items: center; gap: 10px;
    font-family: "Marcellus", Georgia, serif; font-weight: 400;
    color: var(--silver);
  }
  .wordmark .name { font-size: 48px; line-height: 1; }
  .wordmark .sub { font-size: 20px; line-height: 1.2; letter-spacing: .5px; }
  .wordmark.small .name { font-size: 30px; }

  .tagline {
    position: absolute; left: 0; width: 100%; text-align: center;
    font-family: "Arimo", Arial, sans-serif; font-size: 16px;
  }
  .tagline.plain { top: 218px; color: var(--gold); }
  .tagline.band {
    top: 236px; height: 30px; line-height: 30px; color: var(--ink); font-size: 15px;
    background: linear-gradient(180deg, var(--gold-light), var(--gold-deep) 50%, var(--gold-light));
    border-top: 3px solid var(--card-black);
    box-shadow: 0 -4px 0 -1px var(--gold-deep);
  }
  .tagline.box {
    top: 254px; left: 104px; width: 313px; height: 42px; line-height: 42px;
    background: var(--yellow-box); color: var(--ink); font-size: 13px;
  }

  .card-back { background: var(--card-black); }
  .card-back .wave { position: absolute; left: 0; top: 0; }
  .office-box {
    position: absolute; left: 17px; top: 27px; width: 175px; height: 109px;
    border: 1.5px solid var(--gold); border-radius: 18px;
    font-family: "Arimo", Arial, sans-serif; color: var(--white);
    font-size: 12.5px; text-align: center; padding-top: 13px; line-height: 17px;
  }
  .contact-list { list-style: none; margin-top: 5px; }
  .contact-list li { display: flex; justify-content: center; align-items: center; gap: 5px; }
  .contact-list svg { width: 11px; height: 11px; fill: var(--white); }
  .office-right {
    position: absolute; left: 212px; width: 290px; text-align: center;
    font-family: "Arimo", Arial, sans-serif; color: var(--gold); font-size: 12.5px; line-height: 16px;
  }
  .office-right .contact-list svg { fill: var(--gold); }
  .brand-dot {
    position: absolute; left: 91px; top: 166px; width: 46px; height: 46px;
    border-radius: 50%; background: var(--gold-deep);
  }
  .person {
    position: absolute; left: 38px; top: 240px; width: 160px; text-align: center;
    font-family: "Marcellus", Georgia, serif; color: var(--ink);
  }
  .person .name { font-size: 21px; line-height: 1; }
  .person .title { font-family: "Arimo", Arial, sans-serif; font-size: 12px; margin-top: 5px; }
  .website {
    position: absolute; right: 36px; top: 267px;
    font-family: "Arimo", Arial, sans-serif; font-size: 12px; letter-spacing: 1px; color: var(--ink);
  }
</style>
</head>
<body>
<main class="board">

  <h2 class="option-label" style="left:76px; top:16px;">Option 1</h2>
  <h2 class="option-label" style="left:68px; top:697px;">Option 2</h2>
  <h2 class="option-label" style="left:637px; top:697px;">Option 3</h2>

  <!-- Option 1 front -->
  <section class="card card-front" style="left:58px; top:60px;">
    <div class="wordmark" style="left:80px; top:98px;">
      <span class="name">VANTORY</span>
      <span class="sub">WEALTH<br>MANAGEMENT</span>
    </div>
    <p class="tagline plain">Preferred Wealth Management for Select Individuals</p>
  </section>

  <!-- Card back -->
  <section class="card card-back" style="left:612px; top:55px;">
    <svg class="wave" width="520" height="296" viewBox="0 0 520 296" aria-hidden="true">
      <defs>
        <linearGradient id="goldSweep" x1="0" y1="0" x2="1" y2="0">
          <stop offset="0" stop-color="#c98a2c"/>
          <stop offset=".45" stop-color="#f0c46a"/>
          <stop offset=".75" stop-color="#d99c3a"/>
          <stop offset="1" stop-color="#f3cf78"/>
        </linearGradient>
      </defs>
      <path d="M0,234 C70,214 130,207 190,210 C270,215 330,256 410,250 C460,246 495,232 520,218 L520,296 L0,296 Z" fill="url(#goldSweep)"/>
      <path d="M150,208 C250,208 320,254 410,252 C460,250 495,238 520,226" fill="none" stroke="#000" stroke-width="5"/>
      <path d="M150,202 C250,202 320,246 410,244 C460,242 495,228 520,214" fill="none" stroke="#e8b24e" stroke-width="2"/>
    </svg>

    <div class="office-box">
      1626 City name, State name,<br>Country name&nbsp; 34236
      <ul class="contact-list">
        <li><svg viewBox="0 0 10 10"><circle cx="5" cy="5" r="4.5" fill="none" stroke="#fff"/><path d="M3 3h1.5l.5 1.5-.8.6a3 3 0 0 0 1.7 1.7l.6-.8L8 6.5V8A5 5 0 0 1 3 3z"/></svg>234.567.8901</li>
        <li><svg viewBox="0 0 10 10"><rect x="2" y="1" width="6" height="3"/><rect x="1" y="4.5" width="8" height="4.5"/></svg>234.567.8901</li>
        <li><svg viewBox="0 0 10 10"><rect x="3" y="0.5" width="4" height="9" rx="1"/></svg>234.567.8901</li>
      </ul>
    </div>

    <div class="wordmark small" style="left:290px; top:27px;">
      <span class="name">VANTORY</span>
    </div>

    <p class="office-right" style="top:100px;">
      <svg width="11" height="11" viewBox="0 0 10 10" style="fill:var(--gold);vertical-align:-1px"><rect x="0.5" y="2" width="9" height="6"/></svg>
      name@VantoryWealthManagement.com
    </p>
    <div class="office-right" style="top:130px;">
      1626 City name, State name,<br>Country name&nbsp; 34236
      <ul class="contact-list" style="margin-top:14px;">
        <li><svg viewBox="0 0 10 10"><circle cx="5" cy="5" r="4.5" fill="none" stroke="#f3c65c"/><path d="M3 3h1.5l.5 1.5-.8.6a3 3 0 0 0 1.7 1.7l.6-.8L8 6.5V8A5 5 0 0 1 3 3z"/></svg>234.567.8901</li>
        <li><svg viewBox="0 0 10 10"><rect x="2" y="1" width="6" height="3"/><rect x="1" y="4.5" width="8" height="4.5"/></svg>234.567.8901</li>
        <li><svg viewBox="0 0 10 10"><rect x="3" y="0.5" width="4" height="9" rx="1"/></svg>234.567.8901</li>
      </ul>
    </div>

    <span class="brand-dot" aria-hidden="true"></span>
    <div class="person">
      <p class="name">PERSONS NAME</p>
      <p class="title">Designation</p>
    </div>
    <p class="website">www.VANTORYWEALTHMANAGEMENT.com</p>
  </section>

  <!-- Option 2 front -->
  <section class="card card-front" style="left:54px; top:389px;">
    <div class="wordmark" style="left:80px; top:98px;">
      <span class="name">VANTORY</span>
      <span class="sub">WEALTH<br>MANAGEMENT</span>
    </div>
    <p class="tagline band">Preferred Wealth Management for Select Individuals</p>
  </section>

  <!-- Option 3 front -->
  <section class="card card-front" style="left:613px; top:389px;">
    <div class="wordmark" style="left:80px; top:112px;">
      <span class="name">VANTORY</span>
      <span class="sub">WEALTH<br>MANAGEMENT</span>
    </div>
    <p class="tagline box">Preferred Wealth Management for Select Individuals</p>
  </section>

</main>
</body>
</html>
```